TK Stationery - Modern Contemporary

Develop modern template for Letterhead and Stationery (business card, letterhead, envelopes) using the TK Logo and Icon

Colors
0054AA
0677BA
7BADD7
CADEEF
E8F1F8
00AB8E
00BBA5
67D7C9
C6EFE9
E9F9F6
EE7325
F08F49
F5BC92
FAE3D3
FDF4ED
6B429C
8869AF
B7A5CE
E3DAEB
F3F0F8

```html
<!DOCTYPE html>
<html lang="en">
<head>
<meta charset="utf-8">
<title>terra kolto stationery</title>
<link href="https://fonts.googleapis.com/css2?family=Arimo:wght@400;700&family=Questrial&display=swap" rel="stylesheet">
<style>
:root{
  --bg:#aaa9aa;
  --paper:#ffffff;
  --navy:#2b3150;
  --green:#2cb673;
  --orange:#f08a2c;
  --ink:#4a4c55;
  --faint:#efeff2;
  --peach:#fde9dd;
}
*{margin:0;padding:0;box-sizing:border-box}
html,body{width:1200px;height:934px;overflow:hidden}
body{background:var(--bg);position:relative;font-family:"Arimo",Arial,sans-serif;color:var(--ink)}
.sheet{position:absolute;background:var(--paper);overflow:hidden;box-shadow:2px 3px 5px rgba(0,0,0,.25)}
.brand{position:absolute;font-family:"Questrial",sans-serif;color:var(--navy);white-space:nowrap;letter-spacing:.5px;line-height:1}
.monogram{position:absolute;font-family:"Questrial",sans-serif;color:var(--faint);line-height:.8;white-space:nowrap;letter-spacing:-4px}
.dot{position:absolute;border-radius:50%;background:var(--peach)}
.footer{position:absolute;left:0;bottom:0;display:block}
.site{position:absolute;color:#fff;font-weight:700;white-space:nowrap}
.small{position:absolute;font-size:8.5px;line-height:10.5px;white-space:nowrap}
.icon{display:inline-block;vertical-align:-1px;margin-right:4px}

/* letterhead */
.letterhead{left:47px;top:108px;width:507px;height:718px}
.letterhead .brand{left:45px;top:41px;font-size:27px}
.rule-v{position:absolute;top:44px;width:1px;height:21px;background:var(--green)}
.letterhead .rule-h{position:absolute;left:45px;top:72px;width:417px;height:1px;background:var(--green)}
.salutation{position:absolute;left:46px;top:221px;font-family:"Questrial",sans-serif;font-size:12px;font-weight:700;color:var(--ink)}
.body-copy{position:absolute;left:45px;top:254px;width:417px;font-size:8.6px;line-height:10.5px;color:#5c5e66}
.body-copy p{margin-bottom:9px}
.signoff{position:absolute;left:46px;top:470px;font-size:7px;font-weight:700}
.signature{position:absolute;left:46px;top:498px;width:83px;height:27px;background:linear-gradient(90deg,#e4e4e8,#f2f2f4);border-radius:3px}

/* business cards */
.card-front{left:586px;top:113px;width:272px;height:155px}
.card-front .brand{left:15px;top:20px;font-size:18px}
.person{position:absolute;left:15px;top:82px}
.person .name{color:var(--green);font-weight:700;font-size:9.5px;letter-spacing:.2px}
.person .role{font-size:7.5px;color:var(--navy);margin-top:2px}
.card-front .rule-h{position:absolute;left:15px;top:106px;width:242px;height:1px;background:var(--green)}
.card-back{left:880px;top:113px;width:273px;height:155px;background:var(--navy)}
.card-back .brand{left:0;width:100%;text-align:center;top:64px;font-size:24px;color:#fff}

/* envelopes */
.env-back{left:586px;top:301px;width:567px;height:246px}
.flap{position:absolute;left:0;top:0;filter:drop-shadow(0 5px 4px rgba(0,0,0,.18))}
.env-back .brand{left:0;width:100%;text-align:center;top:20px;font-size:25px}
.env-front{left:586px;top:579px;width:567px;height:247px}
.env-front .brand{left:19px;top:15px;font-size:18px}
</style>
</head>
<body>

<section class="sheet letterhead">
  <div class="brand">terra kolto</div>
  <div class="rule-v" style="left:234px"></div>
  <div class="small" style="left:256px;top:45px;color:var(--navy)">
    <svg class="icon" width="7" height="7" viewBox="0 0 10 10"><path d="M2 1l2 2-1 1.5c.8 1.5 1.7 2.4 3 3L7.5 6l2 2-1.5 1.5C4.5 9 1 5.5.5 2.5z" fill="var(--green)"/></svg>555-014-2100<br>
    <svg class="icon" width="7" height="6" viewBox="0 0 10 8"><rect x=".5" y=".5" width="9" height="7" fill="none" stroke="var(--green)"/><path d="M.5 .5L5 4.5 9.5.5" fill="none" stroke="var(--green)"/></svg>info@terrakolto.com
  </div>
  <div class="rule-v" style="left:376px"></div>
  <div class="small" style="right:45px;top:45px;text-align:right;color:var(--navy)">Your address, city<br>state, ZIP 0000</div>
  <div class="rule-h"></div>

  <div class="salutation">Dear Mr. Reyes,</div>
  <div class="body-copy">
    <p>Lorem ipsum dolor sit amet, consectetuer adipiscing elit, sed diam nonummy nibh euismod tincidunt ut laoreet dolore magna aliquam erat volutpat. Ut wisi enim ad minim veniam, quis nostrud exerci tation ullamcorper suscipit lobortis nisl ut aliquip ex ea commodo consequat. Duis autem vel eum iriure dolor in hendrerit in vulputate velit esse molestie consequat, vel illum dolore eu feugiat</p>
    <p>Rorem ipsum dolor sit amet, consectetuer adipiscing elit, sed diam nonummy nibh euismod tincidunt ut laoreet dolore magna aliquam erat volutpat. Ut wisi enim ad minim veniam, quis nostrud exerci tation ullamcorper suscipit lobortis nisl ut aliquip ex ea commodo consequat. Duis autem vel eum iriure dolor in hendrerit in vulputate velit esse molest</p>
    <p>Dorem ipsum dolor sit amet, consectetuer adipiscing elit, sed diam nonummy nibh euismod tincidunt ut laoreet dolore magna aliquam erat volutpat. Ut wisi enim ad minim veniam, quis nostrud exerci tation ullamcorper suscipit lobortis nisl ut aliquip ex ea commodo consequat. Duis autem vel eum iriure dolor in hendrerit in suscipit lobortis nisl ut aliquip ex ea commodo consequat. Duis autem vel eum iriure dolor in hendrerit in vulputate velit esse molestie consequat, vel illum</p>
    <p>Sorem ipsum dolor sit amet, consectetuer adipiscing elit, sed diam nonummy nibh euismod tincidunt ut laoreet dolore magna aliquam erat volutpat. Ut wisi enim ad minim veniam, quis nostrud exerci tation ullamcorper suscipit lobortis nisl ut aliquip ex ea commodo consequat. Duis autem vel eum iriure dolor in</p>
  </div>
  <div class="signoff">Sincerely,</div>
  <div class="signature" role="img" aria-label="Handwritten signature"></div>

  <div class="monogram" style="left:175px;top:505px;font-size:250px">tk</div>
  <div class="dot" style="left:477px;top:506px;width:30px;height:30px"></div>

  <svg class="footer" width="507" height="23" viewBox="0 0 507 23">
    <path d="M0 0H172C180 0 184 11 194 11H507V23H0Z" fill="var(--navy)"/>
    <polygon points="188,5 337,5 340,8 191,8" fill="var(--green)"/>
    <polygon points="341,5 507,5 507,8 344,8" fill="var(--orange)"/>
  </svg>
  <div class="site" style="left:45px;bottom:5px;font-size:11px">www.terrakolto.com</div>
</section>

<section class="sheet card-front">
  <div class="brand">terra kolto</div>
  <div class="monogram" style="left:112px;top:48px;font-size:80px;letter-spacing:-2px">tk</div>
  <div class="dot" style="left:258px;top:39px;width:14px;height:14px"></div>
  <div class="person">
    <div class="name">DANIEL REYES</div>
    <div class="role">Manager</div>
  </div>
  <div class="rule-h"></div>
  <div class="small" style="left:15px;top:113px;font-size:7.5px;line-height:9.5px;color:var(--navy)">
    <svg class="icon" width="6" height="6" viewBox="0 0 10 10"><path d="M2 1l2 2-1 1.5c.8 1.5 1.7 2.4 3 3L7.5 6l2 2-1.5 1.5C4.5 9 1 5.5.5 2.5z" fill="var(--green)"/></svg>555-014-2100<br>
    <svg class="icon" width="6" height="5" viewBox="0 0 10 8"><rect x=".5" y=".5" width="9" height="7" fill="none" stroke="var(--green)"/><path d="M.5 .5L5 4.5 9.5.5" fill="none" stroke="var(--green)"/></svg>info@terrakolto.com
  </div>
  <div class="small" style="right:15px;top:113px;font-size:7.5px;line-height:9.5px;text-align:right;color:var(--navy)">Your address, city<br>state, ZIP 0000</div>
  <svg class="footer" width="272" height="13" viewBox="0 0 272 13">
    <path d="M0 0H113C117 0 119 6 124 6H272V13H0Z" fill="var(--navy)"/>
    <polygon points="120,2 199,2 200,4 121,4" fill="var(--green)"/>
    <polygon points="201,2 272,2 272,4 202,4" fill="var(--orange)"/>
  </svg>
  <div class="site" style="left:17px;bottom:3px;font-size:6.5px">www.terrakolto.com</div>
</section>

<section class="sheet card-back">
  <div class="brand">terra kolto</div>
</section>

<section class="sheet env-back">
  <svg class="flap" width="567" height="80" viewBox="0 0 567 80">
    <path d="M0 0H567L555 50C552 62 545 68 530 68H40C25 68 18 62 14 50Z" fill="var(--paper)"/>
  </svg>
  <div class="brand">terra kolto</div>
</section>

<section class="sheet env-front">
  <div class="brand">terra kolto</div>
  <div class="small" style="left:19px;top:35px;font-size:6.5px;line-height:7.5px;color:var(--navy)">Your address, city<br>state, ZIP 0000</div>
  <div class="monogram" style="left:235px;top:50px;font-size:240px">tk</div>
  <div class="dot" style="left:538px;top:41px;width:30px;height:30px"></div>
  <svg class="footer" width="567" height="23" viewBox="0 0 567 23">
    <path d="M0 0H170C180 0 184 11 196 11H567V23H0Z" fill="var(--navy)"/>
    <polygon points="183,5 383,5 386,8 186,8" fill="var(--green)"/>
    <polygon points="389,5 567,5 567,8 392,8" fill="var(--orange)"/>
  </svg>
  <div class="site" style="left:19px;bottom:5px;font-size:11px">www.terrakolto.com</div>
</section>

</body>
</html>
```